Vantiqo custom business card design

Need a authentic, innovative business card design for a new mobile app business. I am uploading a few screen images from our app for you to view. I would like app design theme to match business card design. I can also send logo images.

```html
<!DOCTYPE html>
<html lang="en">
<head>
<meta charset="utf-8">
<title>Vantiqo Business Card</title>
<link rel="stylesheet" href="https://fonts.googleapis.com/css2?family=Montserrat:wght@700&family=Work+Sans:wght@400;500;600&display=swap">
<style>
  :root {
    --page-bg: #efedea;
    --card-clear: #e8e5e1;
    --card-edge: #d4cfc9;
    --brand-purple: #5c2473;
    --brand-purple-light: #70358a;
    --ink-dark: #231c22;
    --ink-light: #eee6dc;
    --ink-soft: #ddd1d6;
  }
  html, body {
    margin: 0;
    padding: 0;
    width: 1200px;
    height: 1047px;
    overflow: hidden;
    background: var(--page-bg);
  }
  .business-card {
    position: absolute;
    left: 120px;
    top: 263px;
    width: 960px;
    height: 521px;
    border-radius: 18px;
    background: var(--card-clear);
    border: 1px solid var(--card-edge);
    overflow: hidden;
    font-family: "Work Sans", Arial, sans-serif;
  }
  .card-shapes {
    position: absolute;
    inset: 0;
  }
  .wordmark {
    position: absolute;
    left: 42px;
    top: 46px;
    margin: 0;
    font-family: "Montserrat", Arial, sans-serif;
    font-weight: 700;
    font-size: 62px;
    line-height: 1;
    color: var(--ink-light);
    letter-spacing: 0.5px;
  }
  .person {
    position: absolute;
    left: 42px;
    top: 176px;
    color: var(--ink-light);
  }
  .person-name {
    margin: 0;
    font-weight: 500;
    font-size: 32px;
    letter-spacing: 0.8px;
    line-height: 1;
    text-transform: uppercase;
  }
  .person-role {
    margin: 10px 0 0;
    font-size: 22px;
    letter-spacing: 0.6px;
    color: var(--ink-soft);
  }
  .address {
    position: absolute;
    left: 42px;
    top: 262px;
    font-style: normal;
    font-size: 22px;
    line-height: 34px;
    letter-spacing: 0.6px;
    color: var(--ink-soft);
  }
  .contact-list {
    position: absolute;
    left: 42px;
    top: 358px;
    margin: 0;
    padding: 0;
    list-style: none;
    font-size: 22px;
    letter-spacing: 0.6px;
    color: var(--ink-soft);
  }
  .contact-item {
    display: flex;
    align-items: center;
    height: 34px;
  }
  .contact-icon {
    width: 16px;
    height: 16px;
    margin-right: 18px;
    fill: none;
    stroke: var(--ink-soft);
    stroke-width: 1.6;
  }
  .brand-lockup {
    position: absolute;
    left: 600px;
    top: 234px;
    display: flex;
    align-items: center;
  }
  .brand-dot {
    width: 40px;
    height: 40px;
    border-radius: 50%;
    background: var(--brand-purple);
    margin-right: 16px;
  }
  .brand-name {
    font-weight: 600;
    font-size: 46px;
    line-height: 1;
    color: var(--ink-dark);
  }
</style>
</head>
<body>
  <main class="business-card">
    <svg class="card-shapes" width="960" height="521" viewBox="0 0 960 521" aria-hidden="true">
      <defs>
        <linearGradient id="purpleField" x1="0" y1="0" x2="1" y2="1">
          <stop offset="0" stop-color="var(--brand-purple-light)"/>
          <stop offset="1" stop-color="var(--brand-purple)"/>
        </linearGradient>
      </defs>
      <path class="purple-field" d="M0 0 H669 A265 265 0 0 0 669 521 H0 Z" fill="url(#purpleField)"/>
      <path class="divider-crescent" d="M741.5 -4.9 A265 265 0 1 0 741.5 524.9 A265 265 0 0 1 741.5 -4.9 Z" fill="var(--ink-dark)"/>
    </svg>

    <h1 class="wordmark">Vantiqo</h1>

    <div class="person">
      <p class="person-name">Dana Whitfield</p>
      <p class="person-role">Director</p>
    </div>

    <address class="address">
      2457 Harbor Lane<br>
      Port Alder, FL 32990
    </address>

    <ul class="contact-list">
      <li class="contact-item">
        <svg class="contact-icon" viewBox="0 0 16 16"><rect x="4" y="1" width="8" height="14" rx="1.5"/><line x1="7" y1="12.5" x2="9" y2="12.5"/></svg>
        (555) 214-6082
      </li>
      <li class="contact-item">
        <svg class="contact-icon" viewBox="0 0 16 16"><path d="M3 1.5 L6 1.5 L7 5 L5 6.5 C6 9 7 10 9.5 11 L11 9 L14.5 10 L14.5 13 C14.5 14 13.5 14.5 12.5 14.5 C6.5 14 2 9.5 1.5 3.5 C1.5 2.5 2 1.5 3 1.5 Z"/></svg>
        (555) 238-7419
      </li>
      <li class="contact-item">
        <svg class="contact-icon" viewBox="0 0 16 16"><rect x="1.5" y="3.5" width="13" height="9" rx="1"/><path d="M1.5 4 L8 9 L14.5 4"/></svg>
        info@Vantiqo.com
      </li>
      <li class="contact-item">
        <svg class="contact-icon" viewBox="0 0 16 16"><circle cx="8" cy="8" r="6.5"/><ellipse cx="8" cy="8" rx="3" ry="6.5"/><line x1="1.5" y1="8" x2="14.5" y2="8"/></svg>
        www.Vantiqo.com
      </li>
    </ul>

    <div class="brand-lockup">
      <span class="brand-dot"></span>
      <span class="brand-name">Vantiqo</span>
    </div>
  </main>
</body>
</html>
```